Fernhale Business Card Design

We are looking for a fresh business card design for our new logo. We would like a business card that is unique but friendly. We are in the window coverings business offering blinds, shutters and shades for homes.

Target Market(s)

Targeting the end-consumer

Industry/Entity Type

Business

Requirements
Must have
• Must have a dedicates space for a photo of our sales person. Must contain our new logo (attached).

```html
<!DOCTYPE html>
<html lang="en">
<head>
<meta charset="utf-8">
<title>Fernhale Business Card</title>
<link href="https://fonts.googleapis.com/css2?family=Work+Sans:wght@400;500&display=swap" rel="stylesheet">
<style>
  :root {
    --page-bg: #161616;
    --card-white: #ffffff;
    --brand-green: #8cc142;
    --text-grey: #555555;
    --photo-light: #f2f2f2;
    --photo-dark: #2e2e33;
  }
  * { margin: 0; padding: 0; box-sizing: border-box; }
  html, body {
    width: 1200px; height: 897px; overflow: hidden;
    background: var(--page-bg);
    font-family: "Work Sans", Arial, sans-serif;
  }
  .canvas { position: relative; width: 1200px; height: 897px; }
  .card {
    position: absolute; left: 303px; width: 595px; height: 338px;
    border-radius: 20px; overflow: hidden;
  }
  .card-front { top: 92px; background: var(--card-white); }
  .card-back { top: 469px; background: var(--brand-green); }

  .agent-name {
    position: absolute; left: 35px; top: 28px;
    font-size: 24px; font-weight: 500; letter-spacing: 1px;
    color: var(--brand-green);
  }
  .agent-title {
    position: absolute; left: 35px; top: 60px;
    font-size: 14px; letter-spacing: 0.5px; color: var(--text-grey);
  }
  .agent-address {
    position: absolute; left: 34px; top: 134px;
    font-size: 14px; line-height: 17px; color: var(--text-grey);
  }
  .contact-list {
    position: absolute; left: 34px; top: 225px; list-style: none;
  }
  .contact-list li {
    display: flex; align-items: center; height: 19.2px;
    font-size: 14px; color: var(--text-grey);
  }
  .contact-list svg { width: 12px; height: 12px; margin-right: 13px; fill: var(--brand-green); }
  .agent-photo {
    position: absolute; right: 0; top: 0; width: 282px; height: 100%;
    background: linear-gradient(180deg, var(--photo-light) 0%, var(--photo-light) 45%, var(--photo-dark) 46%, var(--photo-dark) 100%);
  }

  .brand {
    position: absolute; left: 0; right: 0; top: 128px;
    display: flex; align-items: center; justify-content: center; gap: 20px;
    color: var(--card-white);
  }
  .brand-square { width: 64px; height: 64px; border: 3px solid var(--card-white); border-radius: 6px; }
  .brand-name { font-size: 66px; font-weight: 500; line-height: 1; }
  .brand-url {
    position: absolute; left: 0; right: 0; top: 298px; text-align: center;
    font-size: 13px; letter-spacing: 0.8px; color: var(--card-white);
  }
</style>
</head>
<body>
<div class="canvas">
  <section class="card card-front">
    <h1 class="agent-name">DANIEL HARTLEY</h1>
    <p class="agent-title">REALTOR</p>
    <p class="agent-address">P.O.Box: 214,<br>Lakeview, Oregon</p>
    <ul class="contact-list">
      <li><svg viewBox="0 0 12 12"><path d="M2.5 0.8 L4.5 3 L3.5 4.6 C4.3 6.2 5.6 7.6 7.3 8.5 L8.9 7.4 L11.2 9.4 L10 11.2 C5.3 10.7 1.2 6.6 0.8 2 Z"/></svg>(012) 555-0148</li>
      <li><svg viewBox="0 0 12 12"><path d="M3 0.5 H9 V11.5 H3 Z M4 1.8 V9.5 H8 V1.8 Z"/></svg>(012) 555-0162</li>
      <li><svg viewBox="0 0 12 12"><path d="M3 0.5 H9 V3.5 H3 Z M1 4 H11 V9 H9 V11.5 H3 V9 H1 Z M4 7.5 V10.5 H8 V7.5 Z"/></svg>(012) 555-0175</li>
      <li><svg viewBox="0 0 12 12"><path d="M0.5 2.5 H11.5 V9.5 H0.5 Z M1.5 3.2 L6 6.4 L10.5 3.2 Z"/></svg>info@fernhale.com</li>
      <li><svg viewBox="0 0 12 12"><circle cx="6" cy="6" r="5.3" fill="none" stroke="#8cc142" stroke-width="1.1"/><path d="M0.7 6 H11.3 M6 0.7 V11.3 M1.6 3.4 H10.4 M1.6 8.6 H10.4" stroke="#8cc142" stroke-width="0.8" fill="none"/><ellipse cx="6" cy="6" rx="2.4" ry="5.3" fill="none" stroke="#8cc142" stroke-width="0.8"/></svg>www.fernhale.com</li>
    </ul>
    <div class="agent-photo" role="img" aria-label="Portrait photo of the sales agent in a dark suit"></div>
  </section>

  <section class="card card-back">
    <div class="brand">
      <span class="brand-square"></span>
      <span class="brand-name">Fernhale</span>
    </div>
    <p class="brand-url">www.fernhalehome.com</p>
  </section>
</div>
</body>
</html>
```